Italian restaurant needs new site

Need to make our website better.

Must have reservation module

Must be able to sell wine tasting tours and wine pairing tours and intégrate with dunmo desk

Blog

Social media

Wandervane ranking and last review.
Updates

Number of Pages Required

1 page

Font styles to use
Serif

Requirements
Must have
• Reservation module
• Marketplace to buy wine pairings and gift certificates
• Wandervane review
• Kindlepost posts
• All info from old site

```html
<!DOCTYPE html>
<html lang="en">
<head>
<meta charset="utf-8">
<title>Vinoro Bistro</title>
<link rel="stylesheet" href="https://fonts.googleapis.com/css2?family=Open+Sans:wght@400;600;700&family=Raleway:wght@400;500;600&display=swap">
<style>
:root{
  --red:#8e2626;
  --red-pill:#b52d2d;
  --orange:#f7941d;
  --orange-light:#fbaa2a;
  --ink:#222;
  --muted:#666;
  --grey-band:#f1f1f3;
  --blue:#1e9fdd;
  --footer:#1b1b1b;
  --green:#34a86e;
  --white:#fff;
}
*{margin:0;padding:0;box-sizing:border-box}
html,body{width:1200px;height:2903px;overflow:hidden;background:var(--white)}
body{position:relative;font-family:"Open Sans",Arial,sans-serif;color:var(--ink)}
.abs{position:absolute}
h1,h2,h3,.heading{font-family:"Raleway","Open Sans",sans-serif;font-weight:500}

/* hero */
.hero{left:0;top:0;width:1200px;height:598px;background:radial-gradient(ellipse at 40% 70%,#6b4a30 0%,#3a2618 45%,#140d09 100%)}
.hero-shade{left:0;top:0;width:1200px;height:598px;background:linear-gradient(180deg,rgba(0,0,0,.55) 0%,rgba(0,0,0,.1) 40%,rgba(0,0,0,.3) 100%)}
.brand{left:90px;top:52px;color:var(--white);font-size:30px;font-weight:400;letter-spacing:1px}
.brand-tag{left:92px;top:94px;color:var(--white);font-size:9px;letter-spacing:1.5px;text-transform:uppercase}
.phone{left:846px;top:34px;color:var(--white);font-size:21px;display:flex;align-items:center;gap:10px}
.social-top{left:996px;top:38px;display:flex;gap:10px}
.social-top span{width:19px;height:19px;background:var(--white);border-radius:2px}
.nav{left:628px;top:92px;display:flex;gap:0;font-size:16px;color:var(--white)}
.nav a{color:var(--white);text-decoration:none;padding:4px 16px;border-radius:14px;margin-right:22px}
.nav a.active{background:var(--red-pill)}
.hero-title{left:0;width:1200px;top:282px;text-align:center;color:var(--white);font-size:48px;font-weight:600;letter-spacing:1px}
.hero-sub{left:0;width:1200px;top:346px;text-align:center;color:var(--white);font-size:25px;font-family:"Open Sans",sans-serif}
.hero-dots{left:1152px;top:276px;display:flex;flex-direction:column;gap:14px}
.hero-dots span{width:6px;height:6px;background:var(--white);border-radius:50%}

/* welcome */
.welcome-photo{left:112px;top:679px;width:420px;height:285px;background:linear-gradient(135deg,#f3c568 0%,#a4713b 45%,#3f3a2a 100%);border:8px solid var(--white);box-shadow:0 2px 10px rgba(0,0,0,.35)}
.welcome-title{left:573px;top:696px;font-size:33px;color:var(--ink)}
.welcome-text{left:573px;top:746px;width:516px;font-size:13.2px;line-height:22px;color:#555;text-align:justify}
.btn-more{left:573px;top:909px;width:116px;height:32px;border-radius:16px;background:var(--orange);color:var(--white);font-size:11px;font-weight:600;display:flex;align-items:center;justify-content:center}

/* menu */
.menu-band{left:0;top:1080px;width:1200px;height:321px;background:var(--grey-band)}
.menu-title{left:0;width:1200px;top:1142px;text-align:center;font-size:30px}
.menu-card{top:1229px;width:290px;height:309px;background:var(--white);border:1px solid #e3e3e3;text-align:center}
.menu-card.featured{box-shadow:0 4px 14px rgba(0,0,0,.25);border-color:#ddd}
.menu-card .dish{width:100%;height:172px}
.menu-card h3{font-family:"Open Sans",sans-serif;font-size:15px;font-weight:400;margin-top:22px}
.menu-card p{font-size:11.5px;line-height:18px;color:#777;margin:8px 28px 0}
.menu-card .view{display:inline-block;margin-top:12px;width:94px;height:24px;border-radius:12px;border:1px solid #c9474a;font-size:11px;line-height:22px;color:#444}
.menu-card.featured .view{background:var(--orange);border-color:var(--orange);color:var(--white)}
.slider-arrow{top:1371px;width:56px;height:56px;border-radius:50%;background:var(--white);border:1px solid #ddd;display:flex;align-items:center;justify-content:center}

/* blogs / reservations */
.blogs{left:0;top:1639px;width:571px;height:404px;background:linear-gradient(120deg,#2a1a16 0%,#5a2a22 50%,#201514 100%)}
.blogs-frame{left:60px;top:1682px;width:453px;height:318px;border:1px solid rgba(255,255,255,.55)}
.blogs-title{left:0;width:571px;top:1805px;text-align:center;color:var(--white);font-size:48px;font-weight:400}
.reserve{left:571px;top:1639px;width:629px;height:404px;background:var(--red)}
.reserve-title{left:615px;top:1681px;color:var(--white);font-size:30px;font-weight:500}
.field{width:244px;height:48px;background:var(--white);border-radius:3px;font-size:13px;color:#888;padding:15px 14px}
.send{left:611px;top:1914px;width:498px;height:46px;background:linear-gradient(180deg,var(--orange-light),var(--orange));border-radius:3px;color:var(--white);font-size:16px;display:flex;align-items:center;justify-content:center}

/* reviews */
.review-brand{left:0;width:1200px;top:2140px;display:flex;justify-content:center;align-items:center;gap:10px;font-size:33px;font-weight:600;color:#111}
.review-brand .mark{width:22px;height:22px;border-radius:50%;background:var(--green)}
.review-card{top:2231px;width:306px;height:153px;background:var(--white);border:1px solid #e4e4e4;box-shadow:0 2px 6px rgba(0,0,0,.12);padding:22px 26px}
.review-card h3{font-family:"Open Sans",sans-serif;font-size:14px;font-weight:400;color:#333}
.review-card p{font-size:11.5px;line-height:18px;color:#888;margin-top:10px}
.review-card .count{color:var(--green);font-size:11.5px}
.rating{display:flex;gap:3px;margin-top:6px}
.rating span{width:11px;height:11px;border-radius:50%;background:var(--green)}
.rating span.half{background:linear-gradient(90deg,var(--green) 50%,#fff 50%);border:1px solid var(--green)}

/* social feed */
.feed{left:0;top:2459px;width:1200px;height:270px;background:linear-gradient(180deg,#1fa2e0,#1a95d3)}
.feed-brand{left:86px;top:2574px;color:var(--white);font-size:28px;font-weight:600}
.feed-handle{left:275px;top:2522px;color:var(--white);font-size:22px}
.feed-text{left:275px;top:2562px;width:812px;color:var(--white);font-size:12.6px;line-height:21px}
.feed-time{left:280px;top:2632px;color:var(--white);font-size:13px;font-style:italic}
.feed-arrows{left:1064px;top:2680px;display:flex;gap:6px}
.feed-arrows span{width:20px;height:20px;border-radius:50%;background:#333;display:flex;align-items:center;justify-content:center}

/* footer */
.footer{left:0;top:2729px;width:1200px;height:174px;background:var(--footer)}
.footer-links{left:0;width:1200px;top:2773px;text-align:center;color:var(--white);font-size:11.5px;letter-spacing:.3px}
.footer-links span{margin:0 10px}
.footer-social{left:0;width:1200px;top:2806px;display:flex;justify-content:center;gap:8px}
.footer-social span{width:25px;height:25px;border:1px solid #aaa;border-radius:50%}
.copyright{left:0;width:1200px;top:2848px;text-align:center;color:var(--white);font-size:12px}
</style>
</head>
<body>

<header>
  <div class="abs hero" role="img" aria-label="Close-up photo of grilled meat and vegetables on a restaurant table"></div>
  <div class="abs hero-shade"></div>
  <div class="abs brand">Vinoro Bistro</div>
  <div class="abs brand-tag">Italian cuisine &amp; wine bar</div>
  <div class="abs phone">
    <svg width="18" height="20" viewBox="0 0 24 24"><path fill="#f7941d" d="M6.6 10.8a15 15 0 0 0 6.6 6.6l2.2-2.2c.3-.3.7-.4 1-.2 1.1.4 2.3.6 3.6.6.6 0 1 .4 1 1V20c0 .6-.4 1-1 1A17 17 0 0 1 3 4c0-.6.4-1 1-1h3.5c.6 0 1 .4 1 1 0 1.3.2 2.5.6 3.6.1.3 0 .7-.2 1z"/></svg>
    555 0142
  </div>
  <div class="abs social-top"><span></span><span></span><span></span><span></span></div>
  <nav class="abs nav">
    <a class="active">HOME</a><a>MENU</a><a>RESERVATIONS</a><a>CONTACTS</a>
  </nav>
  <h1 class="abs hero-title">VINORO BISTRO</h1>
  <div class="abs hero-sub">Italian restaurant in Costa Veranda</div>
  <div class="abs hero-dots"><span></span><span></span><span></span><span></span></div>
</header>

<section class="welcome">
  <div class="abs welcome-photo" role="img" aria-label="Photo of friends toasting with red wine at an outdoor table at sunset"></div>
  <h2 class="abs welcome-title">WELCOME TO VINORO BISTRO</h2>
  <p class="abs welcome-text">Vinoro Bistro Located in the heart of downtown, across from Marisol Square, just two short blocks up from Harborline Resort and the Veranda marina is Vinoro Bistro, a place with great original Southern Italian and Mediterranean cuisine and a European touch. Sure to enjoy your classic favorites or satisfy even the most distinctive pallet We offer, a variety of homemade , fresh cooked dishes derived from generations-old family recipes, accompanied</p>
  <div class="abs btn-more">READ MORE »</div>
</section>

<section class="menu">
  <div class="abs menu-band"></div>
  <h2 class="abs menu-title">MENU</h2>

  <div class="abs slider-arrow" style="left:69px">
    <svg width="14" height="24" viewBox="0 0 14 24"><path d="M12 2 2 12l10 10" fill="none" stroke="#555" stroke-width="2"/></svg>
  </div>
  <div class="abs slider-arrow" style="left:1073px">
    <svg width="14" height="24" viewBox="0 0 14 24"><path d="m2 2 10 10L2 22" fill="none" stroke="#555" stroke-width="2"/></svg>
  </div>

  <article class="abs menu-card" style="left:132px">
    <div class="dish" role="img" aria-label="Photo of baked mussels with tomato on a white plate" style="background:linear-gradient(135deg,#d9a35a,#7a4a22 60%,#c23a2a)"></div>
    <h3>COVERS</h3>
    <p>It has survived not only five centuries, but also the leap into electronic</p>
    <span class="view">View More</span>
  </article>
  <article class="abs menu-card featured" style="left:453px">
    <div class="dish" role="img" aria-label="Photo of glasses of red wine" style="background:linear-gradient(135deg,#e8eaee,#9a9ca4 50%,#5a1015)"></div>
    <h3>RED WINE</h3>
    <p>It has survived not only five centuries, but also the leap into electronic</p>
    <span class="view">View More</span>
  </article>
  <article class="abs menu-card" style="left:772px">
    <div class="dish" role="img" aria-label="Photo of pasta with grilled steak on a plate" style="background:linear-gradient(135deg,#5a2e1a,#c98a48 55%,#e8d2a8)"></div>
    <h3>ANTIPASTOS</h3>
    <p>It has survived not only five centuries, but also the leap into electronic</p>
    <span class="view">View More</span>
  </article>
</section>

<section class="blog-reserve">
  <div class="abs blogs" role="img" aria-label="Photo of a wine bar with bottles and gift boxes"></div>
  <div class="abs blogs-frame"></div>
  <h2 class="abs blogs-title">BLOGS</h2>

  <div class="abs reserve"></div>
  <h2 class="abs reserve-title">RESERVATIONS</h2>
  <div class="abs field" style="left:611px;top:1736px">Name</div>
  <div class="abs field" style="left:865px;top:1736px">Email</div>
  <div class="abs field" style="left:611px;top:1794px">Phone Number</div>
  <div class="abs field" style="left:865px;top:1794px">Date</div>
  <div class="abs field" style="left:611px;top:1852px">Time</div>
  <div class="abs field" style="left:865px;top:1852px">Hotel Name</div>
  <div class="abs send">SEND</div>
</section>

<section class="reviews">
  <div class="abs review-brand"><span class="mark"></span>Wandervane</div>

  <div class="abs review-card" style="left:114px">
    <h3>WANDERVANE TRAVELER RATING</h3>
    <p>It has survived not only five centuries, but also the leap into electronic typesetting,<br><span class="count">Based on 1,086 traveler reviews</span></p>
    <div class="rating"><span></span><span></span><span></span><span></span><span class="half"></span></div>
  </div>
  <div class="abs review-card" style="left:447px">
    <h3>WANDERVANE RANKING</h3>
    <p>It has survived not only five centuries, but also the leap into electronic typesetting,<br><span class="count">Based on 1,086 traveler reviews</span></p>
    <div class="rating"><span></span><span></span><span></span><span></span><span class="half"></span></div>
  </div>
  <div class="abs review-card" style="left:780px">
    <h3>WANDERVANE TRAVELER RATING</h3>
    <p>It has survived not only five centuries, but also the leap into electronic typesetting,<br><span class="count">Based on 1,086 traveler reviews</span></p>
    <div class="rating"><span></span><span></span><span></span><span></span><span class="half"></span></div>
  </div>
</section>

<section class="feed-section">
  <div class="abs feed"></div>
  <div class="abs feed-brand">Chirpline</div>
  <div class="abs feed-handle">VINOROBISTRO</div>
  <p class="abs feed-text">Lorem Ipsum has been the industry's standard dummy text ever since the 1500s, when an unknown printer took a galley of type and scrambled it to make a type specimen book. It has survived not only five centuries, but also the leap into electronic typesetting, remaining essentially unchanged Lorem Ipsum has been the industry's standard dummy text ever since the 1500s, when an unknown printer</p>
  <div class="abs feed-time">1 hr + 53 minus ago</div>
  <div class="abs feed-arrows">
    <span><svg width="8" height="10" viewBox="0 0 8 10"><path d="M6 1 2 5l4 4" fill="none" stroke="#fff" stroke-width="1.6"/></svg></span>
    <span><svg width="8" height="10" viewBox="0 0 8 10"><path d="m2 1 4 4-4 4" fill="none" stroke="#fff" stroke-width="1.6"/></svg></span>
  </div>
</section>

<footer>
  <div class="abs footer"></div>
  <div class="abs footer-links">
    <span>ABOUT</span>|<span>PRIVACY</span>|<span>TERMS</span>|<span>LEGAL</span>|<span>CONTACT</span>
  </div>
  <div class="abs footer-social"><span></span><span></span><span></span><span></span><span></span><span></span></div>
  <div class="abs copyright">Copyright © 2017 All Rights Reserved</div>
</footer>

</body>
</html>
```